Banner Graphics For Veltrin Storefront Page

Hello,
I am looking for a designer to help me with a banner heading that I want to place on my Veltrin storefront page. My company sells outdoor kitchen/bbq island accessories. I would like for it to have a background photo with text/logo & graphics overlaid on the image. If possible I would like it to include the 5 small "benefit boxes" that are attached on the file that features graphics for one of the products that I sell . I have also included a color photo of my products in actual use. Feel free to use it but if you have a better idea of a background image feel free to try it, maybe a lifestyle stock photo?? Or maybe something else?? I am open to all ideas and you are the creative ones:) Feel free to be creative. The pixel requirements for final image is 3,000 pixels by 600 pixels. Let me know if you have any questions. THANKS! P.s. I also included some stock photos that I like to give you some ideas.

```html
<!DOCTYPE html>
<html lang="en">
<head>
<meta charset="utf-8">
<title>Crestline Outdoor Kitchens – Veltrin Storefront Banner</title>
<link href="https://fonts.googleapis.com/css2?family=Cinzel:wght@400;600&family=Roboto+Condensed:wght@400;700&display=swap" rel="stylesheet">
<style>
  :root{
    --stage:#b4b4b4;
    --banner-black:#050505;
    --ink-white:#ffffff;
    --rule:#cfcfcf;
    --wood-dark:#2a1a10;
    --wood-mid:#6b4426;
    --kitchen-light:#e9ecea;
    --kitchen-tile:#a9b8b2;
    --brand-ink:#1d1d1d;
    --badge-border:#8a8a8a;
    --badge-band:#6f6f6f;
    --badge-fill:#ffffff;
    --badge-dark:#1a1a1a;
  }
  *{margin:0;padding:0;box-sizing:border-box;}
  html,body{width:1200px;height:600px;overflow:hidden;}
  body{background:var(--stage);position:relative;font-family:"Roboto Condensed",Arial,sans-serif;}

  .banner{position:absolute;left:53px;top:191px;width:1095px;height:219px;background:var(--banner-black);overflow:hidden;}

  .banner__food-photo{position:absolute;left:0;top:0;width:380px;height:219px;
    background:
      radial-gradient(ellipse 90px 80px at 120px 110px, var(--wood-mid), transparent 100%),
      linear-gradient(90deg, var(--wood-dark) 0%, #1c120b 55%, var(--banner-black) 100%);}

  .banner__kitchen-photo{position:absolute;right:0;top:0;width:266px;height:219px;
    clip-path:polygon(38px 0,100% 0,100% 100%,0 100%);
    background:linear-gradient(180deg,var(--kitchen-light) 0%,#dfe3e1 45%,var(--kitchen-tile) 70%,#8d9c97 100%);}

  .headline{position:absolute;left:240px;width:620px;top:24px;text-align:center;
    font-family:"Cinzel",Georgia,serif;color:var(--ink-white);font-size:31px;letter-spacing:1px;font-weight:400;}
  .headline__rule{position:absolute;left:245px;width:610px;top:66px;height:1px;
    background:linear-gradient(90deg,transparent,var(--rule) 15%,var(--rule) 85%,transparent);}
  .subline{position:absolute;left:240px;width:620px;top:72px;text-align:center;
    font-family:"Cinzel",Georgia,serif;color:var(--ink-white);font-size:15px;letter-spacing:.6px;}

  .benefits{position:absolute;left:404px;top:106px;display:flex;gap:9px;}
  .benefit{width:50px;height:89px;background:var(--badge-fill);border:2px solid var(--badge-border);
    border-radius:7px;overflow:hidden;display:flex;flex-direction:column;align-items:center;}
  .benefit__mark{height:40px;display:flex;align-items:center;justify-content:center;}
  .benefit__label{width:100%;background:var(--badge-band);color:var(--ink-white);font-size:6px;
    font-weight:700;text-align:center;padding:2px 0;letter-spacing:.3px;}
  .benefit__text{font-size:5px;line-height:1.15;text-align:center;color:var(--badge-dark);padding:3px 3px 0;}

  .brand{position:absolute;right:28px;top:24px;display:flex;align-items:center;gap:6px;}
  .brand__square{width:10px;height:10px;background:var(--brand-ink);}
  .brand__name{font-family:"Cinzel",Georgia,serif;color:var(--brand-ink);font-size:20px;line-height:1;}
  .brand__tag{position:absolute;right:40px;top:52px;font-family:"Cinzel",Georgia,serif;color:var(--brand-ink);font-size:10px;letter-spacing:.5px;}
</style>
</head>
<body>
  <section class="banner">
    <div class="banner__food-photo" role="img" aria-label="Grilled steak with rosemary on a wooden cutting board with knife and fork"></div>
    <div class="banner__kitchen-photo" role="img" aria-label="Outdoor kitchen island with stainless steel access doors"></div>

    <h1 class="headline">HAND CRAFTED BBQ ACCESS DOORS</h1>
    <div class="headline__rule"></div>
    <p class="subline">ELEGANT DESIGN WITH DURABLE CONSTRUCTION</p>

    <div class="benefits">
      <div class="benefit">
        <div class="benefit__mark"><svg width="30" height="30"><circle cx="15" cy="15" r="13" fill="none" stroke="#1a1a1a" stroke-width="2"/><rect x="3" y="12" width="24" height="7" fill="#1a1a1a"/></svg></div>
        <div class="benefit__label">QUALITY</div>
        <p class="benefit__text">Our employees take Pride in their Work</p>
      </div>
      <div class="benefit">
        <div class="benefit__mark"><svg width="32" height="28"><rect x="2" y="2" width="28" height="24" fill="none" stroke="#1a1a1a" stroke-width="2"/><rect x="6" y="9" width="20" height="8" fill="#1a1a1a"/></svg></div>
        <div class="benefit__label">VALUE</div>
        <p class="benefit__text">Our doors weigh 10 Pounds More than the competition</p>
      </div>
      <div class="benefit">
        <div class="benefit__mark"><svg width="36" height="26"><rect x="2" y="6" width="32" height="14" fill="#1a1a1a"/></svg></div>
        <div class="benefit__label">STRENGTH</div>
        <p class="benefit__text">Offers higher level of Corrosion Resistance</p>
      </div>
      <div class="benefit">
        <div class="benefit__mark"><svg width="34" height="30"><rect x="3" y="3" width="12" height="24" fill="#1a1a1a"/><rect x="17" y="3" width="3" height="24" fill="#1a1a1a"/><rect x="22" y="8" width="9" height="14" fill="none" stroke="#1a1a1a" stroke-width="1.5"/></svg></div>
        <div class="benefit__label">DURABILITY</div>
        <p class="benefit__text">Thick and Durable Stainless Steel Construction</p>
      </div>
      <div class="benefit">
        <div class="benefit__mark"><svg width="32" height="32"><circle cx="16" cy="16" r="13" fill="#1a1a1a"/><circle cx="16" cy="16" r="8" fill="#fff"/></svg></div>
        <div class="benefit__label">PEACE<br>OF MIND</div>
        <p class="benefit__text">Your Satisfaction is our highest priority</p>
      </div>
    </div>

    <div class="brand">
      <span class="brand__square"></span>
      <span class="brand__name">CRESTLINE</span>
    </div>
    <p class="brand__tag">outdoor kitchens</p>
  </section>
</body>
</html>
```